Birchline Septic Solutions

Would like to see some single sided ones but would also like to see some double sided with one sided only being the logo. Owners name is Colin Vandro. Phone number is 555-214-0387
Services are pumping, inspections, installs, and repairs

Contact Information for Business Card

555-241-0387 Colin Vandro Fernbrook, OH

```html
<!DOCTYPE html>
<html lang="en">
<head>
<meta charset="utf-8">
<title>Birchline Septic Solutions – Business Card</title>
<link href="https://fonts.googleapis.com/css2?family=Montserrat:wght@500;600;700&display=swap" rel="stylesheet">
<style>
  :root {
    --page-bg: #e4e1df;
    --card-light: #f1e8e7;
    --card-dark: #000000;
    --accent-teal: #2bbdb8;
    --ink-dark: #1b1b1b;
    --ink-light: #ffffff;
  }
  * { margin: 0; padding: 0; box-sizing: border-box; }
  html, body {
    width: 1200px;
    height: 900px;
    overflow: hidden;
    background: var(--page-bg);
    font-family: "Montserrat", Arial, sans-serif;
  }
  .business-card {
    position: absolute;
    left: 100px;
    top: 141px;
    width: 1000px;
    height: 618px;
    background: var(--card-light);
    box-shadow: 0 10px 30px rgba(0,0,0,0.18);
    overflow: hidden;
  }
  .card-shapes {
    position: absolute;
    inset: 0;
    width: 1000px;
    height: 618px;
  }
  .shape-dark { fill: var(--card-dark); }
  .shape-accent { fill: var(--accent-teal); }

  .brand-name {
    position: absolute;
    left: 0;
    top: 170px;
    width: 440px;
    text-align: center;
    color: var(--ink-dark);
    font-weight: 700;
    font-size: 36px;
    line-height: 1.2;
    letter-spacing: 2px;
    text-transform: uppercase;
  }

  .contact-block {
    position: absolute;
    left: 570px;
    top: 130px;
    color: var(--ink-light);
  }
  .owner-name {
    color: var(--accent-teal);
    font-weight: 700;
    font-size: 37px;
    letter-spacing: 0.5px;
    line-height: 1;
    margin-bottom: 30px;
  }
  .contact-line {
    display: flex;
    align-items: center;
    font-weight: 500;
    font-size: 29px;
    line-height: 1;
    height: 34px;
    margin-bottom: 4px;
  }
  .contact-icon {
    width: 26px;
    height: 26px;
    margin-right: 20px;
    fill: var(--accent-teal);
    flex: none;
  }
  .service-list {
    position: absolute;
    left: 578px;
    top: 345px;
    list-style: none;
    color: var(--ink-light);
  }
  .service-item {
    display: flex;
    align-items: center;
    font-weight: 500;
    font-size: 29px;
    height: 49px;
    text-transform: uppercase;
  }
  .service-item::before {
    content: "";
    width: 13px;
    height: 13px;
    border-radius: 50%;
    background: var(--accent-teal);
    margin-right: 22px;
  }
</style>
</head>
<body>
  <div class="business-card">
    <svg class="card-shapes" viewBox="0 0 1000 618" aria-hidden="true">
      <path class="shape-accent" d="M438,0 L481,0 C520,70 505,200 455,330 C425,410 408,470 404,520 C408,420 440,330 462,230 C478,140 470,60 438,0 Z"/>
      <path class="shape-dark" d="M481,0 C520,70 505,200 455,330 C400,470 400,560 458,618 L1000,618 L1000,0 Z"/>
    </svg>

    <div class="brand-name">Birchline<br>Septic Solutions</div>

    <div class="contact-block">
      <div class="owner-name">COLIN VANDRO</div>
      <div class="contact-line">
        <svg class="contact-icon" viewBox="0 0 24 24" aria-hidden="true">
          <path d="M6.6 10.8a15.1 15.1 0 0 0 6.6 6.6l2.2-2.2a1 1 0 0 1 1-.25 11.4 11.4 0 0 0 3.6.57 1 1 0 0 1 1 1V20a1 1 0 0 1-1 1A17 17 0 0 1 3 4a1 1 0 0 1 1-1h3.5a1 1 0 0 1 1 1c0 1.25.2 2.45.57 3.57a1 1 0 0 1-.25 1z"/>
        </svg>
        555-214-0387
      </div>
      <div class="contact-line">
        <svg class="contact-icon" viewBox="0 0 24 24" aria-hidden="true">
          <path d="M12 2a7 7 0 0 0-7 7c0 5.2 7 13 7 13s7-7.8 7-13a7 7 0 0 0-7-7zm0 9.5A2.5 2.5 0 1 1 12 6.5a2.5 2.5 0 0 1 0 5z"/>
        </svg>
        Fernbrook, OH
      </div>
    </div>

    <ul class="service-list">
      <li class="service-item">Pumping</li>
      <li class="service-item">Inspections</li>
      <li class="service-item">Installs</li>
      <li class="service-item">Repairs</li>
    </ul>
  </div>
</body>
</html>
```